Business Card Design

I already have a company logo for my company. I have a logo for the manufacturer we represent. I want a professional business card design.

```html
<!DOCTYPE html>
<html lang="en">
<head>
<meta charset="utf-8">
<title>Alertline Group LLC – Business Card</title>
<link rel="stylesheet" href="https://fonts.googleapis.com/css2?family=Open+Sans:wght@400;600;700&display=swap">
<style>
  :root {
    --backdrop-light: #4a4a4a;
    --backdrop-dark: #1b1b1b;
    --card-black: #161616;
    --brand-red: #e31e26;
    --brand-gold: #e0a91f;
    --text-white: #f2f2f2;
  }
  * { box-sizing: border-box; margin: 0; padding: 0; }
  html, body { width: 1200px; height: 780px; overflow: hidden; }
  body {
    background: linear-gradient(135deg, var(--backdrop-light), var(--backdrop-dark));
    font-family: "Open Sans", Arial, sans-serif;
    position: relative;
  }
  .card {
    position: absolute;
    top: 240px;
    width: 520px;
    height: 300px;
    border-radius: 24px;
    background: var(--card-black);
    overflow: hidden;
    box-shadow: 0 18px 40px rgba(0,0,0,.55);
  }
  .card--front { left: 50px; }
  .card--back { left: 630px; }

  .wave { position: absolute; left: 0; bottom: 0; width: 520px; height: 130px; }

  .brand {
    display: flex;
    align-items: center;
    gap: 10px;
    color: var(--text-white);
    font-weight: 700;
    letter-spacing: .5px;
    line-height: 1.05;
  }
  .brand__square { width: 14px; height: 14px; background: var(--brand-red); flex: none; }

  .card--front .brand {
    position: absolute;
    left: 34px;
    top: 58px;
    font-size: 22px;
    width: 210px;
  }
  .divider {
    position: absolute;
    left: 262px;
    top: 42px;
    width: 1px;
    height: 150px;
    background: var(--brand-red);
  }
  .contact {
    position: absolute;
    left: 282px;
    top: 44px;
    color: var(--text-white);
    font-size: 13.5px;
    line-height: 1.4;
  }
  .contact__name {
    color: var(--brand-red);
    font-weight: 600;
    font-size: 20px;
    letter-spacing: .3px;
    line-height: 1.1;
  }
  .contact__role { margin-bottom: 8px; }
  .contact__line { display: flex; align-items: center; gap: 6px; }
  .contact__line svg { width: 11px; height: 11px; flex: none; }
  .contact__address { margin-top: 2px; }

  .card--back { display: flex; align-items: center; justify-content: center; }
  .card--back .brand { font-size: 34px; }
</style>
</head>
<body>

<section class="card card--front" aria-label="Business card front">
  <svg class="wave" viewBox="0 0 520 130" aria-hidden="true">
    <path d="M0 30 C 110 20, 200 60, 300 95 S 460 128, 520 124 L520 130 L0 130 Z" fill="var(--brand-gold)"/>
    <path d="M0 40 C 110 32, 200 72, 300 104 S 460 130, 520 130 L0 130 Z" fill="var(--brand-red)"/>
  </svg>

  <div class="brand"><span class="brand__square"></span><span>ALERTLINE GROUP LLC</span></div>

  <div class="divider"></div>

  <div class="contact">
    <p class="contact__name">DANA WHITLOCK</p>
    <p class="contact__role">Managing Director</p>
    <p class="contact__line">
      <svg viewBox="0 0 12 12"><path d="M2.5 1h2l1 3-1.3 1a6 6 0 0 0 2.8 2.8L8 6.5l3 1v2c0 .8-.7 1.5-1.5 1.5A8.5 8.5 0 0 1 1 2.5C1 1.7 1.7 1 2.5 1z" fill="var(--brand-red)"/></svg>
      123 456 789
    </p>
    <p class="contact__line">
      <svg viewBox="0 0 12 12"><rect x="1" y="2.5" width="10" height="7" rx="1" fill="var(--brand-red)"/><path d="M1.5 3l4.5 3.5L10.5 3" stroke="var(--card-black)" fill="none"/></svg>
      info@yourmail.com
    </p>
    <p class="contact__line">
      <svg viewBox="0 0 12 12"><circle cx="6" cy="6" r="5" fill="var(--brand-red)"/><path d="M1 6h10M6 1c-2 2-2 8 0 10M6 1c2 2 2 8 0 10" stroke="var(--card-black)" stroke-width=".8" fill="none"/></svg>
      www.yourwebsite.com
    </p>
    <p class="contact__address">Your address, City<br>State, Zip 1234</p>
  </div>
</section>

<section class="card card--back" aria-label="Business card back">
  <div class="brand"><span class="brand__square"></span><span>ALERTLINE<br>GROUP LLC</span></div>
</section>

</body>
</html>
```